Evaporative Air Conditioning Summer Service

Would like to design a flyer to send out in an email to existing clients to promote a Pre-summer service for Evaporative Air Conditioners
Cost will be $110.00 inc gst
Tasks included in service are
- Inspection and clean of pads
- Inspection and check float valve, water pump, fan, motor, bearings, drain
- Clean basin
- Supply of bacterial tablet
- Inspect overall condition of unit
- Any repairs if required will be quoted
Please see files attached of a previous very basic flyer I have used for installation and replacement unit costs. This has current contact information
Have also uploaded company logo for use.
Thanks
Plumbing

```html
<!DOCTYPE html>
<html lang="en">
<head>
<meta charset="utf-8">
<title>Pre-Summer Service Flyer</title>
<link rel="stylesheet" href="https://fonts.googleapis.com/css2?family=Oswald:wght@600;700&family=Exo+2:ital,wght@0,500;0,600;0,700;1,400&family=Roboto:wght@400;500&display=swap">
<style>
  :root {
    --backdrop: #767676;
    --paper: #ffffff;
    --band: #555559;
    --gold: #f4a81d;
    --brand-blue: #1f5faa;
    --pill-blue: #1471b8;
    --price-top: #6f9bd4;
    --price-bottom: #1a4fa0;
    --text-dark: #222222;
    --tick: #f29a1f;
    --cta-top: #f2c10f;
    --cta-bottom: #ef6a32;
  }
  * { margin: 0; padding: 0; box-sizing: border-box; }
  html, body { width: 1200px; height: 1200px; overflow: hidden; }
  body { background: var(--backdrop); position: relative; font-family: "Roboto", Arial, sans-serif; }

  .flyer {
    position: absolute; left: 200px; top: 35px;
    width: 800px; height: 1131px;
    background: var(--paper); overflow: hidden;
  }
  .hero-photo {
    position: absolute; left: 0; top: 0; width: 800px; height: 532px;
    background: linear-gradient(100deg, #f3e4da 0%, #f1dccd 35%, #eae4dc 60%, #e3e0da 100%);
  }
  .hero-photo::after {
    content: ""; position: absolute; left: 0; bottom: 0; width: 100%; height: 60px;
    background: linear-gradient(180deg, rgba(94,150,110,0) 0%, rgba(94,150,110,.45) 100%);
  }
  .logo-panel { position: absolute; left: 0; top: 370px; width: 800px; height: 162px; }
  .brand {
    position: absolute; left: 64px; top: 432px;
    display: flex; align-items: center; gap: 12px;
  }
  .brand-dot { width: 46px; height: 46px; border-radius: 50%; background: var(--brand-blue); }
  .brand-name {
    font-family: "Exo 2", Arial, sans-serif; font-weight: 700;
    font-size: 27px; line-height: 1.05; color: var(--brand-blue); letter-spacing: .5px;
  }

  .title-band {
    position: absolute; left: 0; top: 530px; width: 800px; height: 159px;
    background: var(--band); text-align: center;
  }
  .headline {
    font-family: "Oswald", Impact, sans-serif; font-weight: 700;
    font-size: 84px; line-height: 1; color: var(--gold);
    margin-top: 14px; letter-spacing: -1px;
  }
  .subhead {
    font-family: "Exo 2", Arial, sans-serif; font-weight: 600;
    font-size: 40px; color: #fff; margin-top: 4px; line-height: 1.1;
  }
  .subhead em { font-weight: 400; font-style: italic; }

  .tech-photo {
    position: absolute; left: 0; top: 777px; width: 320px; height: 354px;
    background: linear-gradient(160deg, #f2f4f6 0%, #e4e8ec 55%, #9fb9d6 100%);
  }
  .price-badge {
    position: absolute; left: 94px; top: 703px; width: 218px; height: 218px;
    border-radius: 50%; border: 2px solid #fff;
    background: linear-gradient(180deg, var(--price-top) 0%, var(--price-bottom) 100%);
    display: flex; flex-direction: column; align-items: center; justify-content: center;
    font-family: "Oswald", Impact, sans-serif; font-weight: 600; color: #fff;
    box-shadow: 0 0 0 1px rgba(26,79,160,.6);
  }
  .price-amount { font-size: 52px; line-height: 1.05; }
  .price-tax { font-size: 42px; line-height: 1.05; }

  .includes-pill {
    position: absolute; left: 350px; top: 716px; width: 204px; height: 40px;
    border-radius: 12px; background: var(--pill-blue); color: #fff;
    font-family: "Exo 2", Arial, sans-serif; font-weight: 700; font-size: 25px;
    line-height: 40px; padding-left: 30px;
  }
  .service-list {
    position: absolute; left: 380px; top: 768px; list-style: none;
    font-size: 17.5px; color: var(--text-dark); line-height: 22.8px;
  }
  .service-list li { position: relative; padding-left: 26px; }
  .service-list svg { position: absolute; left: 0; top: 4px; }

  .cta {
    position: absolute; left: 304px; top: 959px; width: 496px; height: 172px;
    border-top-left-radius: 90px;
    background: linear-gradient(180deg, var(--cta-top) 0%, #f39a22 55%, var(--cta-bottom) 100%);
    color: #fff; text-align: center; padding-left: 22px;
  }
  .cta-label {
    font-family: "Exo 2", Arial, sans-serif; font-weight: 600; font-size: 31px;
    margin-top: 17px; line-height: 1;
  }
  .cta-phone {
    font-family: "Exo 2", Arial, sans-serif; font-weight: 600; font-size: 58px;
    line-height: 1; margin-top: 6px; letter-spacing: 2px;
  }
  .cta-email { font-size: 16.5px; margin-top: 4px; }
  .cta-abn { font-size: 16px; margin-top: 10px; }
  .cta-abn strong { font-family: "Exo 2", Arial, sans-serif; font-weight: 700; letter-spacing: .5px; }
</style>
</head>
<body>
  <main class="flyer">
    <div class="hero-photo" role="img" aria-label="Row of white air conditioning outdoor units along a wall"></div>
    <svg class="logo-panel" viewBox="0 0 800 162" aria-hidden="true">
      <path d="M0 10 H350 C440 10 470 60 490 110 C505 145 510 162 510 162 H0 Z" fill="#ffffff"/>
    </svg>
    <div class="brand">
      <span class="brand-dot"></span>
      <span class="brand-name">KEYSTONE<br>GAS &amp; PLUMBING</span>
    </div>

    <header class="title-band">
      <h1 class="headline">PRE-SUMMER SERVICE</h1>
      <p class="subhead"><em>for</em> Evaporative Air Conditioners</p>
    </header>

    <div class="tech-photo" role="img" aria-label="Technician in blue shirt and cap servicing a wall-mounted air conditioner"></div>
    <div class="price-badge">
      <span class="price-amount">$110.00</span>
      <span class="price-tax">inc GST</span>
    </div>

    <div class="includes-pill">INCLUDES</div>
    <ul class="service-list">
      <li><svg width="16" height="16" viewBox="0 0 16 16"><circle cx="8" cy="8" r="8" fill="var(--tick)"/><path d="M4.3 8.3l2.4 2.3 5-5" stroke="#fff" stroke-width="2" fill="none"/></svg>Inspection &amp; clean of pads</li>
      <li><svg width="16" height="16" viewBox="0 0 16 16"><circle cx="8" cy="8" r="8" fill="var(--tick)"/><path d="M4.3 8.3l2.4 2.3 5-5" stroke="#fff" stroke-width="2" fill="none"/></svg>Inspection &amp; check float valve,<br>water pump, fan, motor, bearings, drain</li>
      <li><svg width="16" height="16" viewBox="0 0 16 16"><circle cx="8" cy="8" r="8" fill="var(--tick)"/><path d="M4.3 8.3l2.4 2.3 5-5" stroke="#fff" stroke-width="2" fill="none"/></svg>Clean basin</li>
      <li><svg width="16" height="16" viewBox="0 0 16 16"><circle cx="8" cy="8" r="8" fill="var(--tick)"/><path d="M4.3 8.3l2.4 2.3 5-5" stroke="#fff" stroke-width="2" fill="none"/></svg>Supply of bacterial tablet</li>
      <li><svg width="16" height="16" viewBox="0 0 16 16"><circle cx="8" cy="8" r="8" fill="var(--tick)"/><path d="M4.3 8.3l2.4 2.3 5-5" stroke="#fff" stroke-width="2" fill="none"/></svg>Inspect overall condition of unit</li>
      <li><svg width="16" height="16" viewBox="0 0 16 16"><circle cx="8" cy="8" r="8" fill="var(--tick)"/><path d="M4.3 8.3l2.4 2.3 5-5" stroke="#fff" stroke-width="2" fill="none"/></svg>Any repairs if required will be quoted</li>
    </ul>

    <section class="cta">
      <p class="cta-label">CALL US TODAY</p>
      <p class="cta-phone">0491570156</p>
      <p class="cta-email">admin@keystonegasplumbing.com.au</p>
      <p class="cta-abn">ABN <strong>11223344556</strong></p>
    </section>
  </main>
</body>
</html>
```